TolVex BIM business website

I have a logo design and business card concept is ongoing at this point, but i need a website design based on VDC or BIM ("Virtual Building and Construction" or "Building Information Modeling") that will stand out for the quality and concept that we provide. I am a consultant providing training and production work for Planwright (Quorvane application <where most of the overview can be obtained>). We are providing BIM production and coordination services as well. I can fill in the meat but I need an open development website. Currently, just obtaining a domain so it can be included on a business card is the quickest objective, then developing the content and launching it.

```html
<!DOCTYPE html>
<html lang="en">
<head>
<meta charset="utf-8">
<title>TolVex BIM Consulting</title>
<link href="https://fonts.googleapis.com/css2?family=Jost:wght@400;500;600&family=Open+Sans:wght@400;600;700&display=swap" rel="stylesheet">
<style>
:root{
  --navy:#1d2c5e;
  --navy-deep:#16234d;
  --footer:#1b2f78;
  --footer-bar:#1f2a4a;
  --orange:#f7a93b;
  --orange-dark:#f39c25;
  --text:#2b2b2b;
  --muted:#8c8c8c;
  --white:#ffffff;
  --card-line:#e3e3e3;
}
*{margin:0;padding:0;box-sizing:border-box}
html,body{width:1200px;height:3103px;overflow:hidden}
body{position:relative;background:var(--white);font-family:"Open Sans",Arial,sans-serif;color:var(--text)}
.abs{position:absolute}
h1,h2,h3,h4{font-family:"Jost",Arial,sans-serif;font-weight:400}

/* hero */
.hero{left:0;top:0;width:1200px;height:683px;
  background:linear-gradient(110deg,#3a3f8a 0%,#2a2f6e 40%,#252a5a 70%,#1c2048 100%);
  clip-path:polygon(0 0,100% 0,100% 628px,0 683px)}
.hero-photo{left:330px;top:100px;width:870px;height:583px;
  background:radial-gradient(ellipse at 45% 40%,rgba(220,200,255,.55),rgba(110,110,190,.25) 45%,rgba(30,30,70,0) 75%)}
.nav{left:0;top:0;width:1200px;height:124px;background:rgba(22,32,80,.55)}
.nav a{position:absolute;top:70px;font-size:14px;font-weight:600;color:var(--white);text-decoration:none;letter-spacing:.3px;text-transform:uppercase}
.nav .active{left:114px;top:62px;width:72px;height:34px;border:2px solid var(--white);text-align:center;line-height:30px;color:var(--orange)}
.brand{left:520px;top:18px;width:160px;text-align:center}
.brand-name{display:inline-flex;align-items:center;gap:8px;font-family:"Jost",Arial,sans-serif;font-size:34px;font-weight:600;color:var(--orange);line-height:1}
.brand-dot{width:14px;height:14px;border-radius:50%;background:var(--orange)}
.brand-sub{font-family:"Jost",Arial,sans-serif;font-size:13px;letter-spacing:3px;color:var(--orange);margin-top:8px}
.hero-title{left:118px;top:280px;font-size:42px;line-height:46px;color:var(--white)}
.btn{display:block;text-align:center;font-size:14px;color:var(--white);text-transform:uppercase;font-family:"Open Sans",Arial,sans-serif}
.hero-btn{left:120px;top:391px;width:145px;height:36px;line-height:36px;background:#4b6aa8}
.dots{left:130px;top:452px;display:flex;gap:9px}
.dots span{width:14px;height:14px;border-radius:50%;background:#9aa0c4}
.dots span:first-child{background:transparent;border:2px solid #9aa0c4}

/* about */
.about-img{left:134px;top:703px;width:435px;height:383px;
  background:radial-gradient(ellipse at 50% 50%,#d6d6d6,#ececec 55%,#ffffff 80%)}
.about-title{left:598px;top:752px;font-size:36px;color:var(--text)}
.body-copy{font-size:15px;line-height:26px;color:var(--muted)}
.about-p1{left:602px;top:818px;width:470px}
.about-p2{left:602px;top:932px;width:470px}
.btn-orange{background:var(--orange);height:37px;line-height:37px}
.about-btn{left:602px;top:1012px;width:147px}

/* services */
.services{left:0;top:1117px;width:1200px;height:497px;background:var(--orange);
  clip-path:polygon(0 0,100% 73px,100% 414px,0 497px)}
.services-title{left:0;top:1218px;width:1200px;text-align:center;font-size:35px;color:var(--white)}
.service-icon{width:124px;height:124px;top:1320px;border:2px solid var(--white);border-radius:50%}
.service-title{top:1322px;width:300px;font-size:22px;line-height:26px;color:var(--white)}
.service-copy{top:1392px;width:260px;font-size:14px;line-height:21px;color:var(--white)}
.service-more{top:1470px;font-size:14px;color:var(--white);text-transform:uppercase}

/* bim */
.bim{left:0;top:1531px;width:1200px;height:538px;
  background:linear-gradient(90deg,#eef5fa 0%,#e3eef7 35%,#bcd6ee 65%,#8fb8e0 100%);
  clip-path:polygon(0 83px,100% 0,100% 500px,0 538px)}
.bim-photo{left:600px;top:1560px;width:600px;height:480px;
  background:radial-gradient(ellipse at 55% 45%,rgba(255,255,255,.75),rgba(160,200,235,.35) 50%,rgba(120,170,220,0) 80%)}
.bim-kicker{left:128px;top:1694px;font-size:29px;color:var(--text)}
.bim-title{left:128px;top:1730px;font-size:35px;color:var(--text)}
.bim-copy{left:128px;top:1784px;width:470px;color:#9a9a9a}
.btn-navy{background:var(--navy-deep);height:36px;line-height:36px}
.bim-btn{left:128px;top:1924px;width:145px}

/* projects */
.projects-title{left:124px;top:2114px;font-size:33px;color:var(--orange)}
.card{top:2183px;width:300px;height:362px;border:1px solid var(--card-line);background:var(--white);box-shadow:0 2px 6px rgba(0,0,0,.06)}
.card-media{width:100%;height:186px}
.card-body{padding:20px 24px 0}
.card-title{font-size:22px;color:var(--text)}
.card-copy{margin-top:6px;font-size:12.5px;line-height:18px;color:#777}
.card-more{display:block;margin-top:6px;font-size:13px;color:var(--text);text-transform:uppercase}

/* footer */
.footer{left:0;top:2638px;width:1200px;height:387px;
  background:linear-gradient(135deg,#24399a 0%,#1b2f78 55%,#162764 100%);
  clip-path:polygon(0 52px,100% 0,100% 100%,0 100%)}
.footer-col{top:2752px}
.footer-col h4{font-family:"Open Sans",Arial,sans-serif;font-size:16px;font-weight:700;color:var(--white);text-transform:uppercase;margin-bottom:22px}
.footer-col li{list-style:none;font-size:15px;line-height:30px;color:#dfe5f5}
.contact-line{font-size:15px;line-height:24px;color:#dfe5f5}
.social{display:flex;gap:4px;margin-top:14px}
.social span{width:30px;height:30px;border:2px solid var(--white);border-radius:50%}
.footer-bar{left:0;top:3025px;width:1200px;height:78px;background:var(--footer-bar);
  text-align:center;line-height:78px;font-size:12px;color:#aab2c8}
</style>
</head>
<body>

<!-- hero -->
<div class="abs hero"></div>
<div class="abs hero-photo" role="img" aria-label="Businessman touching a holographic city model of skyscrapers rising from a tablet over blue architectural wireframes"></div>

<nav class="abs nav">
  <a class="active" href="#">Home</a>
  <a href="#" style="left:209px">About Us</a>
  <a href="#" style="left:314px">Services</a>
  <a href="#" style="left:416px">Blogs</a>
  <a href="#" style="left:722px">Team</a>
  <a href="#" style="left:799px">Projects</a>
  <a href="#" style="left:904px">Training</a>
  <a href="#" style="left:1008px">Contact</a>
</nav>
<div class="abs brand">
  <div class="brand-name"><span class="brand-dot"></span>TolVex</div>
  <div class="brand-sub">BIM CONSULTING</div>
</div>

<h1 class="abs hero-title">Virtual Building and<br>Construction</h1>
<a class="abs btn hero-btn" href="#">Learn More</a>
<div class="abs dots"><span></span><span></span><span></span><span></span></div>

<!-- about -->
<div class="abs about-img" role="img" aria-label="White 3D cutaway model of a building floor plan"></div>
<h2 class="abs about-title">About Company</h2>
<p class="abs body-copy about-p1">Fusce ultricies orci ac feugiat suscipit leo massa sodales velit et scelerisque mi tortor at ipsum cligula augue bibendum accumsan vestibulum ut commodo a mi Morbi ornare gravida elit Integer congue augue et malesuada</p>
<p class="abs body-copy about-p2">Iaculis ipsum dui aliquet felis at cursus magna nisl nec elit Praesent elementum elit at tellus nec ultricies sit</p>
<a class="abs btn btn-orange about-btn" href="#">Learn More</a>

<!-- services -->
<div class="abs services"></div>
<h2 class="abs services-title">Our Services</h2>

<div class="abs service-icon" style="left:118px">
  <svg width="120" height="120" viewBox="0 0 120 120" fill="none" stroke="#fff" stroke-width="2">
    <rect x="38" y="32" width="46" height="30"/>
    <polyline points="46,54 56,46 64,50 76,40"/>
    <circle cx="40" cy="72" r="6"/><path d="M30 90v-4a10 10 0 0 1 20 0v4"/>
    <circle cx="60" cy="72" r="6"/><path d="M50 90v-4a10 10 0 0 1 20 0v4"/>
    <circle cx="80" cy="72" r="6"/><path d="M70 90v-4a10 10 0 0 1 20 0v4"/>
  </svg>
</div>
<h3 class="abs service-title" style="left:257px">We Provide Training and Production work for Planwright</h3>
<p class="abs service-copy" style="left:257px">Ae et malesuada iaculis ipsum dui aliquet felis at cursus magna nisl nec elit Praesent elementum eli</p>
<a class="abs service-more" style="left:257px" href="#">Read More</a>

<div class="abs service-icon" style="left:588px">
  <svg width="120" height="120" viewBox="0 0 120 120" fill="none" stroke="#fff" stroke-width="2">
    <circle cx="60" cy="60" r="10"/>
    <circle cx="60" cy="60" r="17" stroke-dasharray="6 4"/>
    <path d="M34 52a28 28 0 0 1 46-16"/><polyline points="80,28 80,36 72,36"/>
    <path d="M86 68a28 28 0 0 1-46 16"/><polyline points="40,92 40,84 48,84"/>
  </svg>
</div>
<h3 class="abs service-title" style="left:728px">We are providing BIM production and Coordination</h3>
<p class="abs service-copy" style="left:728px">Ae et malesuada iaculis ipsum dui aliquet felis at cursus magna nisl nec elit Praesent elementum eli</p>
<a class="abs service-more" style="left:728px" href="#">Read More</a>

<!-- bim -->
<div class="abs bim"></div>
<div class="abs bim-photo" role="img" aria-label="Young businessman reaching toward a glowing holographic city wireframe"></div>
<h2 class="abs bim-kicker">We Provide Building</h2>
<h2 class="abs bim-title">Information Modelling</h2>
<p class="abs body-copy bim-copy">Fusce ultricies orci ac feugiat suscipit leo massa sodales velit et scelerisque mi tortor at ipsum cligula augue bibendum accumsan vestibulum ut commodo a mi Morbi ornare gravida elit Integer congue augue et malesuada</p>
<a class="abs btn btn-navy bim-btn" href="#">Learn More</a>

<!-- projects -->
<h2 class="abs projects-title">Latest Projects</h2>

<article class="abs card" style="left:118px">
  <div class="card-media" role="img" aria-label="Glass office tower against a blue sky" style="background:linear-gradient(135deg,#1e4f86,#5d9ccd 55%,#b8d6ea)"></div>
  <div class="card-body">
    <h3 class="card-title">Blog Tittle here</h3>
    <p class="card-copy">sociosqu ad litora torquent per conubia nostra per inceptos hymenaeos Proin nulla arcu nonummy luctus dictum eget</p>
    <a class="card-more" href="#">Read More</a>
  </div>
</article>

<article class="abs card" style="left:445px">
  <div class="card-media" role="img" aria-label="Business team meeting in front of a sunset city skyline" style="background:linear-gradient(180deg,#e9b07a,#d98a4e 50%,#7d6a62)"></div>
  <div class="card-body">
    <h3 class="card-title">Blog Tittle here</h3>
    <p class="card-copy">sociosqu ad litora torquent per conubia nostra per inceptos hymenaeos Proin nulla arcu nonummy luctus dictum eget</p>
    <a class="card-more" href="#">Read More</a>
  </div>
</article>

<article class="abs card" style="left:770px">
  <div class="card-media" role="img" aria-label="Looking up at skyscrapers under a bright sky" style="background:linear-gradient(160deg,#b9d2ea,#3d6aa3 50%,#1a2f5a)"></div>
  <div class="card-body">
    <h3 class="card-title">Blog Tittle here</h3>
    <p class="card-copy">sociosqu ad litora torquent per conubia nostra per inceptos hymenaeos Proin nulla arcu nonummy luctus dictum eget</p>
    <a class="card-more" href="#">Read More</a>
  </div>
</article>

<!-- footer -->
<div class="abs footer"></div>

<div class="abs footer-col" style="left:137px">
  <h4>Company</h4>
  <ul><li>About Us</li><li>What We do</li><li>Team</li><li>Clients</li></ul>
</div>
<div class="abs footer-col" style="left:325px">
  <h4>Our Services</h4>
  <ul><li>Virtual Building</li><li>Building Information Modelling</li><li>Training &amp; Production</li><li>Coordination</li></ul>
</div>
<div class="abs footer-col" style="left:619px;top:2748px">
  <h4>Resources</h4>
  <ul><li>Blogs</li><li>News</li><li>Projects</li><li>Contact</li></ul>
</div>
<div class="abs footer-col" style="left:803px">
  <h4>Contact Us</h4>
  <p class="contact-line">48 Ridgefield Avenue Suite 12, Austin TX 73301</p>
  <p class="contact-line">555.014.2290</p>
  <p class="contact-line">hello@tolvex.example</p>
  <div class="social"><span></span><span></span><span></span><span></span></div>
</div>

<div class="abs footer-bar">© 2017 Company Name. All right reserved  Term of Use</div>

</body>
</html>
```